Marlowe Hullcraft

Creating a brochure for company that manufactures boats. 8x11
Cover: Black w/boat pictures (just the boat, not the background)
1st inside page: Maybe a gray background of some sort (fade).
2nd inside page:same
Back Cover: Black background

Please feel free to ask questions. Photos on the design have the name of the pic.

Target Market(s)

- Companies that sell boats
- Individuals looking for a new boat

Industry/Entity Type

It Company

Requirements
Must have
• The brochure must have 4 pages and use all of the photos provided in the slots notes on the handwritten design idea.

```html
<!DOCTYPE html>
<html lang="en">
<head>
<meta charset="utf-8">
<title>Marlowe Hullcraft – Standards, Options &amp; Features</title>
<link href="https://fonts.googleapis.com/css2?family=Roboto+Condensed:wght@400;700&family=Michroma&family=Exo+2:ital,wght@1,700&display=swap" rel="stylesheet">
<style>
  :root {
    --backdrop: #ececec;
    --page-black: #05070d;
    --water-top: #2f5f8f;
    --water-mid: #14386a;
    --water-deep: #081a3e;
    --band-edge: #5a6a88;
    --header-cyan: #3fc0e3;
    --row-blue: #dcf0fb;
    --row-white: #ffffff;
    --grid-line: #9db8cc;
    --cell-text: #1d2a3a;
    --light-text: #e8eef6;
  }
  * { box-sizing: border-box; margin: 0; padding: 0; }
  html, body { width: 1200px; height: 1000px; overflow: hidden; }
  body { background: var(--backdrop); position: relative; font-family: "Roboto Condensed", sans-serif; }

  .spec-sheet {
    position: absolute; left: 272px; top: 50px; width: 655px; height: 900px;
    background: var(--page-black); overflow: hidden;
  }
  .water-photo {
    position: absolute; left: 0; top: 36px; width: 100%; height: 812px;
    background: linear-gradient(180deg, var(--water-top) 0%, var(--water-mid) 40%, var(--water-deep) 80%, #050c1f 100%);
  }
  .top-band, .bottom-band {
    position: absolute; left: 0; width: 100%;
    background: linear-gradient(180deg, #0b0e18, #000);
  }
  .top-band { top: 0; height: 36px; border-bottom: 3px solid var(--band-edge); }
  .bottom-band { bottom: 0; height: 52px; border-top: 3px solid var(--band-edge); }

  .brand-badge { position: absolute; left: 205px; top: 36px; width: 245px; height: 58px; }
  .brand-name {
    position: absolute; left: 205px; top: 46px; width: 245px; text-align: center;
    font-family: "Michroma", sans-serif; font-size: 17px; color: var(--light-text); letter-spacing: 1px;
  }
  .sheet-title {
    position: absolute; left: 0; top: 102px; width: 100%; text-align: center;
    font-family: "Michroma", sans-serif; font-size: 12px; letter-spacing: 2px;
    font-variant: small-caps; color: var(--light-text);
  }
  .boat-photo { position: absolute; top: 128px; height: 26px; border-radius: 3px; }
  .boat-a { left: 302px; width: 82px; background: linear-gradient(90deg, #e6dfb0, #f4f0d8); }
  .boat-b { left: 404px; width: 76px; background: linear-gradient(90deg, #b8c3cc, #e3e8ec); }
  .boat-c { left: 498px; width: 82px; background: linear-gradient(90deg, #3fc5c3, #d8eef0); }

  .feature-table {
    position: absolute; left: 66px; top: 157px; width: 523px;
    border-collapse: collapse; table-layout: fixed;
    box-shadow: 0 6px 14px rgba(0,0,0,.5);
  }
  .feature-table col.col-feature { width: 229px; }
  .feature-table col.col-model { width: 98px; }
  .feature-table th {
    background: var(--header-cyan); height: 15px; font-size: 11px; line-height: 15px; padding: 0 4px;
  }
  .feature-table th.label { color: #fff; text-align: left; font-weight: 700; }
  .feature-table th.model { font-family: "Exo 2", sans-serif; font-style: italic; color: #0d1a2a; font-size: 11px; }
  .feature-table td {
    height: 16.2px; font-size: 9.5px; line-height: 15px; color: var(--cell-text);
    border: 1px solid var(--grid-line); padding: 0 4px; text-align: center; white-space: nowrap;
  }
  .feature-table td:first-child { text-align: left; }
  .feature-table tbody tr:nth-child(odd) td { background: var(--row-blue); }
  .feature-table tbody tr:nth-child(even) td { background: var(--row-white); }

  .site-url {
    position: absolute; left: 0; bottom: 14px; width: 100%; text-align: center;
    font-size: 15px; color: var(--light-text); letter-spacing: .3px;
  }
</style>
</head>
<body>
<main class="spec-sheet">
  <div class="water-photo" role="img" aria-label="Photograph of rippled open ocean water"></div>
  <div class="top-band"></div>
  <div class="bottom-band"></div>

  <svg class="brand-badge" viewBox="0 0 245 58" aria-hidden="true">
    <polygon points="0,0 245,0 225,58 20,58" fill="#0a0d16" stroke="#6c7a94" stroke-width="1.5"/>
  </svg>
  <div class="brand-name">MARLOWE HULLCRAFT</div>

  <h1 class="sheet-title">Standards, options &amp; features</h1>

  <div class="boat-photo boat-a" role="img" aria-label="Photo of the 220 Bay boat"></div>
  <div class="boat-photo boat-b" role="img" aria-label="Photo of the 260 Bay boat"></div>
  <div class="boat-photo boat-c" role="img" aria-label="Photo of the 262 CC boat"></div>

  <table class="feature-table">
    <colgroup><col class="col-feature"><col class="col-model"><col class="col-model"><col class="col-model"></colgroup>
    <thead>
      <tr><th class="label">STANDARD FEATURES</th><th class="model">220 Bay</th><th class="model">260 Bay</th><th class="model">262 CC</th></tr>
    </thead>
    <tbody>
      <tr><td>• Jack Plate - Hydraulic</td><td>S</td><td>S</td><td>N/A</td></tr>
      <tr><td>• Cushions - Removable Bow</td><td>O</td><td>O</td><td>S</td></tr>
      <tr><td>• Seat - Cooler Seat with Backrest - Forward of Console</td><td>S</td><td>S</td><td>S</td></tr>
      <tr><td>• Battery Compartment</td><td>S</td><td>S</td><td>S</td></tr>
      <tr><td>• Livewells - Transom Bait Station</td><td>S</td><td>S</td><td>S</td></tr>
      <tr><td>• Automatic Bilge Pump</td><td>S</td><td>S</td><td>S</td></tr>
      <tr><td>• Compass</td><td>S</td><td>S</td><td>S</td></tr>
      <tr><td>• Washdown - Fresh Water</td><td>O</td><td>O</td><td>O</td></tr>
      <tr><td>• Washdown - Raw Water</td><td>O</td><td>O</td><td>O</td></tr>
      <tr><td>• Lights - Navigation</td><td>S</td><td>S</td><td>S</td></tr>
      <tr><td>• Pop Up Cleats - Stainless Steel</td><td>S</td><td>S</td><td>S</td></tr>
      <tr><td>• Stainless Steel Cleats</td><td>O</td><td>O</td><td>O</td></tr>
      <tr><td>• Switch Panel w/ Breakers - Water Resistant</td><td>S</td><td>S</td><td>S</td></tr>
      <tr><td>• Stainless Bow and Stern Eyes</td><td>S</td><td>S</td><td>S</td></tr>
      <tr><td>• Stainless Steering Wheel</td><td>S</td><td>S</td><td>S</td></tr>
      <tr><td>• Vacuum Bagged Hull</td><td>S</td><td>S</td><td>S</td></tr>
      <tr><td>• Bow Casting Platform with Storage</td><td>S</td><td>S</td><td>S</td></tr>
      <tr><td>• Hydraulic Steering</td><td>O</td><td>O</td><td>S</td></tr>
      <tr><td>• Stern Casting Platform</td><td>S</td><td>S</td><td>N/A</td></tr>
      <tr><td>• Anchor Storage</td><td>S</td><td>S</td><td>S</td></tr>
      <tr><td>• Tackle Station - Integrated in Helm Seat</td><td>S</td><td>S</td><td>S</td></tr>
      <tr><td>• Drink Holders</td><td>S (2)</td><td>S (4)</td><td>S (6)</td></tr>
      <tr><td>• Cushions - Aft Seat(s)</td><td>S</td><td>S</td><td>S</td></tr>
      <tr><td>• Head - Enclosed Porcelain SeaFlush</td><td>N/A</td><td>N/A</td><td>S</td></tr>
      <tr><td>• Rod Holders - GunwaleMount (6)</td><td>S (4)</td><td>S (6)</td><td>S (6)</td></tr>
      <tr><td>• Steering - Tilt</td><td>S</td><td>S</td><td>S</td></tr>
      <tr><td>• GPS Chart Plotter</td><td>O</td><td>O</td><td>O</td></tr>
      <tr><td>• Rub Rail - Upgraded Stainless Steel Insert</td><td>S</td><td>S</td><td>S</td></tr>
      <tr><td>• Stereo - Tidewave Audio - 4 Speakers - MP3 - 12 V Adapter</td><td>S</td><td>S</td><td>S</td></tr>
      <tr><td>• Stereo Upgrade - Subwoofer - Power Amp</td><td>O</td><td>O</td><td>O</td></tr>
      <tr><td>• Trim Tabs</td><td>O</td><td>O</td><td>O</td></tr>
      <tr><td>• Lockable Console Storage</td><td>S</td><td>S</td><td>S</td></tr>
      <tr><td>• Prop(s) -Keelson PowerMatched - Stainless Steel</td><td>S</td><td>S</td><td>S</td></tr>
      <tr><td>• Top - Bimini Top - ColorMatched</td><td>O</td><td>O</td><td>O</td></tr>
      <tr><td>• Top - T-Top with Canvas</td><td>O</td><td>O</td><td>N/A</td></tr>
      <tr><td>• T-Top with Hard Top - Custom Design with “M” Mark</td><td>N/A</td><td>N/A</td><td>S</td></tr>
      <tr><td>• Rod Holders - T-Top</td><td>N/A</td><td>N/A</td><td>S</td></tr>
      <tr><td>• Lights - Cockpit (2)</td><td>S</td><td>S</td><td>S</td></tr>
      <tr><td>• Warranty - Limited Lifetime</td><td>S</td><td>S</td><td>S</td></tr>
      <tr><td>• Ladder - Dive / Swim Ladder</td><td>O</td><td>O</td><td>S</td></tr>
      <tr><td>Seats - Helm - Upgraded with Flip Up Bolsters</td><td>S</td><td>S</td><td>S</td></tr>
    </tbody>
  </table>

  <p class="site-url">www.marlowehullcraft.com</p>
</main>
</body>
</html>
```